printing company neeeds a trifold design

I need a trifold brochure (8.5 x 11) flat size, then folded to a trifold that will highlight about a dozen of my most popular products. Should be modern, with just enough of a sales tool. I attached a few thing that I have but looking for something special. I can supply images or you can use place holders?
Updates

The brochure with the "eye" on the front panel is my most current trifold and you can follow that for most of the content. I might edit that later on

Please DO NOT copy my design. Looking for something fresh, new and interesting. I added my old one to show some content and images.
Thanks all!!!!

good morning I am looking for something different. Fresh, modern, clean (neeeds to be cohesive and able to be branded for social media, postcards etc.) and No "eye" or just a small one. . You can use some of the pics and some of the content. This needs to be sales piece I sent out to prospective clients.
Show that we are professional, personal and do great work. 3rd generation printer that is responsive and reaches out to all that respond. All types of Printing, Large format like signs and banners, Realesate, small biz, trade show products look at kornbluthpress.com

Designs look the same

Target Market(s)

Small business, real eststate firms, local business, professionals

Industry/Entity Type

I am in the printing and sign business... 2 of my websites are kornbluthpress.com and kornbluthtypeworks.com

Requirements
Must have
• a front panel with contact info and company logo that I can send over, a panel about my company and images
Nice to have
• something stylish, easy to read with impact. Needs to be something people will wanty to knao more abouit and top reach out
Should not have
• The same look as what I sent over.

```html
<!DOCTYPE html>
<html lang="en">
<head>
<meta charset="utf-8">
<title>Kornbluth Press Trifold – Inside Spread</title>
<link rel="stylesheet" href="https://fonts.googleapis.com/css2?family=Arimo:wght@400;700&family=Roboto:ital,wght@0,300;0,400;1,300&display=swap">
<style>
  :root {
    --backdrop: #595759;
    --navy: #35318f;
    --white: #ffffff;
    --label-blue: #1c9ad8;
    --highlight: #f4ec1c;
    --purple-top: #3b3a98;
    --magenta-mid: #a52a8c;
    --magenta-bottom: #e4127b;
    --ink: #3a3a3a;
  }
  * { margin: 0; padding: 0; box-sizing: border-box; }
  html, body { width: 1200px; height: 971px; overflow: hidden; background: var(--backdrop); }
  .sheet { position: absolute; left: 92px; top: 91px; width: 1017px; height: 788px; overflow: hidden; background: var(--white); }

  /* Services panel */
  .swatch-backdrop { position: absolute; left: 0; top: 0; width: 337px; height: 788px;
    background: linear-gradient(160deg, #9fd6ef 0%, #43c2b5 18%, #7a7fd6 45%, #c55fc8 70%, #ea3c8c 88%, #d9d9e0 100%); }
  .services-card { position: absolute; left: 26px; top: 50px; width: 311px; height: 738px; background: var(--white); }
  .services-title { position: absolute; left: 36px; top: 31px; font-family: "Arimo", Arial, sans-serif; font-weight: 700;
    font-size: 34px; line-height: 30.5px; letter-spacing: -0.8px; color: var(--navy); }
  .services-list { position: absolute; left: 36px; top: 144px; list-style: none;
    font-family: "Roboto", Arial, sans-serif; font-weight: 300; font-size: 16.5px; line-height: 30.5px; color: var(--ink); }
  .services-list li::before { content: "•"; font-size: 11px; margin-right: 6px; vertical-align: 2px; }

  /* Product photography */
  .photo { position: absolute; }
  .photo-menus { left: 337px; top: 0; width: 314px; height: 204px; background: linear-gradient(135deg, #2b2a2c, #c8a07a 55%, #b3322c); }
  .photo-postcards { left: 337px; top: 204px; width: 234px; height: 159px; background: linear-gradient(135deg, #1f2a36, #6a7f8f 50%, #e0d9cf); }
  .photo-brochures { left: 337px; top: 363px; width: 234px; height: 157px; background: linear-gradient(135deg, #9b1e24, #2c3a48 50%, #1d5f74); }
  .photo-aframe { left: 571px; top: 204px; width: 191px; height: 316px; background: var(--white); }
  .photo-aframe-sign { position: absolute; left: 18px; top: 30px; width: 150px; height: 240px;
    background: linear-gradient(180deg, #1c1c1c 0%, #7a4a2a 30%, #b86a3a 60%, #1c1c1c 100%); }
  .photo-cards { left: 337px; top: 520px; width: 406px; height: 268px; background: linear-gradient(135deg, #e6e1d8, #5a3b2a 45%, #e04a5a 75%, #dfe6e0); }

  .tag { position: absolute; background: var(--label-blue); color: var(--white);
    font-family: "Arimo", Arial, sans-serif; font-weight: 700; font-size: 10.5px; line-height: 15px; padding: 0 5px; }
  .tag-menus { left: 497px; top: 189px; width: 154px; text-align: center; }
  .tag-postcards { left: 337px; top: 204px; width: 78px; }
  .tag-brochures { left: 337px; top: 363px; width: 146px; }
  .tag-cards { left: 337px; top: 520px; width: 148px; }
  .tag-aframe { left: 571px; top: 473px; width: 78px; height: 47px; line-height: 10px; padding-top: 3px; }

  /* Promise panel */
  .promise-panel { position: absolute; left: 651px; top: 0; width: 366px; height: 788px;
    background: linear-gradient(180deg, var(--purple-top) 0%, var(--magenta-mid) 50%, var(--magenta-bottom) 100%); color: var(--white); }
  .promise-copy { position: absolute; left: 762px; width: 255px; top: 0; text-align: center; color: var(--white); }
  .promise-intro { position: absolute; left: 0; width: 100%; top: 64px; font-family: "Roboto", Arial, sans-serif; font-weight: 300; font-size: 13.5px; }
  .promise-heading { position: absolute; left: 0; width: 100%; top: 80px; font-family: "Arimo", Arial, sans-serif; font-weight: 700;
    font-size: 25px; line-height: 25.5px; letter-spacing: -0.5px; }
  .promise-heading .highlight { background: var(--highlight); color: var(--navy); padding: 0 2px; }
  .promise-lead { position: absolute; left: 0; width: 100%; font-family: "Roboto", Arial, sans-serif; font-weight: 300; font-size: 18px; line-height: 20px; }
  .lead-help { top: 179px; }
  .lead-owner { top: 225px; }
  .promise-rule { position: absolute; left: 105px; top: 282px; width: 45px; height: 1px; background: rgba(255,255,255,0.55); }
  .promise-small { position: absolute; left: -20px; width: 295px; font-family: "Roboto", Arial, sans-serif; font-weight: 300; font-size: 10.3px; line-height: 14px; }
  .small-speed { top: 300px; }
  .small-contact { top: 328px; font-style: italic; }
  .small-human { top: 356px; }
  .spectrum-line { position: absolute; left: 857px; top: 459px; width: 44px; height: 3px;
    background: linear-gradient(90deg, #e23b8c, #7a63d6, #3cc3b0); }
  .tagline { position: absolute; left: 784px; top: 530px; font-family: "Arimo", Arial, sans-serif; font-weight: 700;
    font-size: 34px; line-height: 31px; letter-spacing: -0.6px; color: var(--white); }
  .website { position: absolute; left: 801px; top: 751px; font-family: "Roboto", Arial, sans-serif; font-weight: 400; font-size: 10.5px; color: var(--white); }
</style>
</head>
<body>
<main class="sheet">
  <section class="services-panel">
    <div class="swatch-backdrop" role="img" aria-label="Close-up photo of colour swatch book fanned out"></div>
    <div class="services-card">
      <h1 class="services-title">OUR PRINTING<br>SERVICES<br>INCLUDE:</h1>
      <ul class="services-list">
        <li>Business Cards</li>
        <li>Brochures &amp; Menus</li>
        <li>Postcards</li>
        <li>Presentation Folders</li>
        <li>Booklets &amp; Catalogs</li>
        <li>Raffle Tickets</li>
        <li>Letterpress Printing</li>
        <li>Wedding Invitations</li>
        <li>Save the Date Items</li>
        <li>Business Announcements</li>
        <li>Greeting Cards</li>
        <li>Signs &amp; Banners</li>
        <li>Retractable Banners</li>
        <li>A-Frame Signs &amp; Flags</li>
        <li>Event Tents</li>
        <li>Posters</li>
        <li>Canvas Prints</li>
        <li>and more</li>
      </ul>
    </div>
  </section>

  <section class="promise-panel"></section>

  <section class="product-gallery">
    <div class="photo photo-menus" role="img" aria-label="Photo of printed tri-fold menus and flyers standing upright"></div>
    <div class="photo photo-postcards" role="img" aria-label="Photo of an assortment of printed postcards"></div>
    <div class="photo photo-brochures" role="img" aria-label="Photo of printed brochures and booklets"></div>
    <div class="photo photo-aframe">
      <div class="photo-aframe-sign" role="img" aria-label="Photo of a black A-frame sidewalk sign holding a printed poster"></div>
    </div>
    <div class="photo photo-cards" role="img" aria-label="Photo of printed business cards and wedding tags"></div>
    <span class="tag tag-menus">TRI-FOLD MENUS &amp; FLYERS</span>
    <span class="tag tag-postcards">POSTCARDS</span>
    <span class="tag tag-brochures">BROCHURES &amp; BOOKLETS</span>
    <span class="tag tag-cards">BUSINESS CARDS &amp; TAGS</span>
    <span class="tag tag-aframe">A-FRAME<br>SIGNS,<br>POSTERS &amp;<br>BANNERS</span>
  </section>

  <div class="promise-copy">
    <p class="promise-intro">At Kornbluth Press</p>
    <h2 class="promise-heading">CUSTOMER<br>SERVICE IS OUR<br><span class="highlight">#1 PRIORITY!</span></h2>
    <p class="promise-lead lead-help">Help and Advice<br>when you need it.</p>
    <p class="promise-lead lead-owner">You will always work<br>with the Owner.</p>
    <div class="promise-rule"></div>
    <p class="promise-small small-speed">Fast Response Time • Personalized Service</p>
    <p class="promise-small small-contact">Available by Email and Phone</p>
    <p class="promise-small small-human">Never a Chat Box • No Robots<br>No Endless Phone Loops When you Call</p>
  </div>
  <div class="spectrum-line"></div>
  <p class="tagline">PRINTING.<br>SIGNS.<br>INVITATIONS.</p>
  <p class="website">kornbluthpress.com</p>
</main>
</body>
</html>
```